Creative Realtor Business Card Design

I need a creative business card.... I would like it to be larger than the normal size...heavy stock.... colorful...
As you are probably aware, there are tons of realtors, and most of their cards ALL look alike.. potential clients are looking for agents that are professional, but are different.
Cards are a form of advertising and I need your help to make mine stand out in a professional, classy way.
I don't need to use the harbor pine realty logo, my personal logo is MORE important for branding purposes. OR..what is your opinion?
YOU DESIGN FOR ME PLEASE! If I could do what you do I would.... I can't and I need your professional help.

                                        If you think I need the card to be double sided so it doesn't look busy by all means I will happily accept double sided. 

I am very interested in a more "creative" card than a standard run of the mill realtor card.    I care about my clients LONG after the sale has closed!

                                   

THANK YOU SO MUCH FOR YOUR EFFORTS AND TALENTS....I APPRECIATE IT SO MUCH! 

                                        Would it be possible to use my theme of my logo to design my card?

                                            Guiding Families to Homes They Love

                              

 

Please make cards larger size .... See this link for ideas that appeal to me. Thank you for your interest.

https://www.findquarry.example/search?q=examples+of+unique+business+cards

I want my card to stand out in size and design...

Thank you so much for your hard work for me.

Lorna

 

Reason: I learned that many designers are very busy. I am providing more time and money in hopes that designers will find it an attractive enough challenge to participate. My business cards are one of my most important marketing materials...I NEED THEM TO BE DISTINCTIVE, CLASSY, and INFORMATIVE. Thank you SO MUCH....and I will be anxiously awaiting your great designs... Lorna

Hello Designers,

Thank you to all you creative people that have kindly offered to submit your creative design(s) for my business card.  I view your designs as your creative artwork. I am anxious to see where your creativity leads you.

I wanted to share with you that my logo was something I personally designed after being in business for 3  years. ( I did have to have a professionals like yourselves draw it for me). The design and logo captured perfectly how I felt about my work ...helping individuals, such as you, find a home.  A house is easy to find, but a home is a place that has "good" energy ... a place where you feel comfortable and can grow.  A place that just "Feels right!"  It's one of those things that you just KNOW when it is right! 

I hope by sharing this bit of information about me can help you creatively design my card for me...I care for my clients LONG after the transaction has closed and they are in their home. Thank you again for taking the time to work on my design. I have been adding money so that your time spent on my card is worth it.

I do need my card soon...so please, if you have a design...submit it!

Kind Regards,

Lorna

Target Market(s)

I have a variety of clients from a mobile home of $35,000 to an estate property for $5M. I feel comfortable working with all types of people...I love my job...I love helping people find the right home because we all know how our home environment affects our well being.

Industry/Entity Type

Advertising

Contact Information for Business Card

Lorna Bratt, Realtor
Harbor Pine Realty
"Guiding Families to Homes They Love"
www.lornanestfinder.example
lbratt@mailvale.example
(555) 418-2053
BRE #04817532, Exp. 8/15

Colors

Designer to choose colors to be used in the design.

Requirements
Must have
• By law, my license number information MUST be on my card.
Nice to have
• I would love card to be memorable...if that is possible for a business card. Also, I would like my card to be larger than the average card. Not sure that is possible either.

```html
<!DOCTYPE html>
<html lang="en">
<head>
<meta charset="utf-8">
<title>Lorna Bratt Realtor – Business Card</title>
<link href="https://fonts.googleapis.com/css2?family=Roboto+Condensed:wght@700&family=Roboto:ital,wght@0,100;0,300;1,300&display=swap" rel="stylesheet">
<style>
  :root {
    --brand-red: #b51c2e;
    --brand-grey: #c8c8cb;
    --card-white: #ffffff;
    --card-edge: #d4d3d8;
    --backdrop: #e6e5e9;
  }
  html, body {
    margin: 0;
    width: 1200px;
    height: 900px;
    overflow: hidden;
    background: var(--backdrop);
  }
  .card-sheet {
    position: relative;
    width: 1200px;
    height: 900px;
  }
  .card {
    position: absolute;
    top: 320px;
    width: 540px;
    height: 261px;
    filter: drop-shadow(0 4px 8px rgba(0,0,0,0.22));
  }
  .card--front { left: 40px; }
  .card--back { left: 620px; }

  .heavy { font-family: "Roboto Condensed", "Arial Narrow", sans-serif; font-weight: 700; }
  .thin { font-family: "Roboto", "Helvetica Neue", sans-serif; font-weight: 100; }
  .light { font-family: "Roboto", "Helvetica Neue", sans-serif; font-weight: 300; }

  .front-shape { fill: var(--brand-red); }
  .front-trim { fill: none; stroke: var(--card-white); stroke-width: 3; }
  .tagline { fill: var(--card-white); font-style: italic; font-size: 11px; }
  .name-first { fill: var(--card-white); font-size: 82px; }
  .name-last { fill: var(--brand-grey); font-size: 62px; }
  .title-word { fill: var(--card-white); font-size: 62px; }

  .back-shape { fill: var(--card-white); stroke: var(--card-edge); stroke-width: 1; }
  .mark-dot { fill: var(--brand-red); }
  .mark-name { fill: var(--brand-red); font-size: 16px; }
  .back-name { fill: var(--brand-red); font-size: 30px; }
  .back-small { fill: var(--brand-red); font-size: 8.5px; }
  .back-phone { fill: var(--brand-red); font-size: 15px; }
  .bracket { fill: none; stroke: var(--brand-red); stroke-width: 0.8; }
</style>
</head>
<body>
<main class="card-sheet">

  <svg class="card card--front" viewBox="0 0 460 222" role="group" aria-label="Card front">
    <path class="front-shape" d="M0,0 H312 L320,86 L382,18 L460,118 V222 H0 Z"/>
    <polyline class="front-trim" points="300,4 308,92 382,28 452,124"/>
    <text class="tagline light" x="40" y="27">“Guiding Families to Homes They Love”</text>
    <text class="name-first heavy" x="12" y="124">LORNA</text>
    <text x="12" y="200">
      <tspan class="name-last heavy">BRATT</tspan><tspan class="title-word thin" dx="6">REALTOR</tspan>
    </text>
  </svg>

  <svg class="card card--back" viewBox="0 0 460 222" role="group" aria-label="Card back">
    <path class="back-shape" d="M0.5,122 L64,60 L126,118 L140,0.5 H459.5 V221.5 H0.5 Z"/>
    <circle class="mark-dot" cx="64" cy="148" r="22"/>
    <text class="mark-name heavy" x="64" y="196" text-anchor="middle">Lorna Bratt</text>

    <text class="back-name heavy" x="322" y="76">LORNA</text>
    <text class="back-name heavy" x="322" y="108">BRATT</text>
    <text class="back-small light" x="322" y="124">Realtor Harbor Pine Realty</text>

    <path class="bracket" d="M326,136 H322 V158 H326"/>
    <text class="back-phone thin" x="330" y="153">(555) 418-2053</text>
    <path class="bracket" d="M434,136 H438 V158 H434"/>

    <text class="back-small light" x="322" y="176">lbratt@mailvale.example</text>
    <text class="back-small light" x="322" y="186">www.lornanestfinder.example</text>
    <text class="back-small light" x="322" y="196">BRE #04817532, Exp. 8/15</text>
  </svg>

</main>
</body>
</html>
```